Design a web site for my business - Brightline Coatings Co.

We are a family business that handles design, fabrication and installation of powder coated aluminum, stainless steel and glass products. Including handrails, privacy slat screens, electric gates and pool fencing. We are based in the Whitsundays in North Queensland and service an area from Airlie Beach to Townsville.

Target Market(s)

Domestic and commercial

Industry/Entity Type

fabrication - manufacturing

Coding

Coded - Design and coding required

Number of Pages Required

5+ page

Colors
0054AA
0677BA
7BADD7
CADEEF
E8F1F8

Requirements
Must have
• photo galleries, contact page, one page for privacy screens, balustrades, glass fencing, stainless steel handrail, powder coated aluminium handrails and pool fencing

```html
<!DOCTYPE html>
<html lang="en">
<head>
<meta charset="utf-8">
<title>Brightline Coatings Co — Design. Fabrication. Installation.</title>
<link href="https://fonts.googleapis.com/css2?family=Poppins:wght@500;600;700&family=Arimo:wght@400;600;700&display=swap" rel="stylesheet">
<style>
:root{
  --navy:#3a5373;
  --navy-dark:#344a66;
  --sage:#4f6a5f;
  --sage-light:#6f8a7f;
  --ink:#1f2a36;
  --text:#3b4450;
  --sky:#e8f1f8;
  --sky-2:#cadeef;
  --map:#c7d2dc;
  --white:#ffffff;
}
*{box-sizing:border-box;margin:0;padding:0}
html,body{width:1200px;height:5115px;overflow:hidden}
body{position:relative;background:var(--white);font-family:'Arimo',Arial,sans-serif;color:var(--text)}
.abs{position:absolute}
.photo{position:absolute;border-radius:10px;overflow:hidden}
h1,h2,h3,.poppins{font-family:'Poppins',Arial,sans-serif}

/* hero */
.hero{left:0;top:0;width:1200px;height:832px;background:linear-gradient(180deg,#9cbad6 0%,#c3d6e4 30%,#6f9a6a 55%,#3f6a3c 80%,#b9a98a 100%)}
.logo{left:140px;top:60px;display:flex;align-items:center;gap:8px;font-family:'Poppins',sans-serif;font-weight:600;font-size:15px;color:var(--navy-dark)}
.logo i{width:18px;height:18px;border-radius:50%;background:var(--navy-dark);display:block}
.nav{left:398px;top:34px;width:802px;height:62px;background:var(--sage);border-radius:31px 0 0 31px;display:flex;align-items:center;padding-left:46px;gap:44px}
.nav a{color:var(--white);font-weight:700;font-size:15px;text-decoration:none;position:relative}
.nav a.active::before{content:"";position:absolute;left:0;right:0;top:-10px;height:2px;background:var(--white)}
.hero-card{left:140px;top:238px;width:484px;height:358px;background:rgba(255,255,255,.88);border-radius:20px;padding:34px 42px}
.hero-card h1{font-size:50px;line-height:60px;font-weight:700;color:var(--ink)}
.hero-card h1 span{color:var(--sage)}
.hero-card p{font-size:13.5px;line-height:19px;color:var(--ink);margin-top:14px;width:400px}
.btn{display:inline-flex;align-items:center;justify-content:center;gap:10px;height:42px;border-radius:21px;color:var(--white);font-weight:700;font-size:13px}
.btn-navy{background:var(--navy)}
.btn-sage{background:var(--sage)}
.hero-btns{display:flex;gap:10px;margin-top:16px}
.circle-btn{width:40px;height:40px;border-radius:50%;background:var(--white);display:flex;align-items:center;justify-content:center}
.features{left:60px;top:752px;width:1080px;height:132px;background:var(--white);border-radius:66px;box-shadow:0 8px 26px rgba(0,0,0,.14);display:flex;align-items:center;justify-content:space-around;padding:0 60px}
.feature{display:flex;align-items:center;gap:14px;font-weight:700;font-size:13.5px;color:var(--ink);line-height:19px}
.feature .ico{width:52px;height:52px;border-radius:50%;background:#eef1f0;display:flex;align-items:center;justify-content:center}
.fdiv{width:1px;height:60px;background:#cfd6d3}

/* headings */
.sec-title{font-size:46px;font-weight:700;color:var(--navy);line-height:52px}
.underline{height:3px;background:var(--navy);border-radius:2px}
.subtitle{font-family:'Poppins',sans-serif;font-weight:600;font-size:19px;color:var(--sage)}
.body{font-size:14.5px;line-height:24px;color:var(--ink)}

/* services */
.svc{position:absolute;top:1703px;width:370px;height:394px;border-radius:14px;border:1px solid #cfd6d3}
.svc-label{position:absolute;top:2058px;width:306px;height:64px;border-radius:14px;background:var(--sage);color:var(--white);font-weight:700;font-size:23px;display:flex;align-items:center;justify-content:center}
.small-arrow{width:42px;height:42px;border-radius:50%;background:#e4e7e6;display:flex;align-items:center;justify-content:center}

/* area */
.area{left:0;top:2868px;width:1200px;height:810px;background:linear-gradient(180deg,#e8f1f8 0%,#dde9f3 60%,#b9cad8 100%)}
.area-map{left:140px;top:3115px;width:526px;height:461px;border-radius:14px;background:linear-gradient(160deg,#d3dde6 0%,var(--map) 100%)}
.area-card{left:765px;top:3114px;width:288px;height:444px;background:var(--white);border-radius:10px;padding:12px}
.area-card ul{list-style:none;border:2px solid var(--navy);border-radius:18px;height:100%;padding:22px 0 0 40px}
.area-card li{display:flex;align-items:center;gap:28px;height:64px;font-weight:700;font-size:16px;color:var(--ink)}
.area-card li i{width:26px;height:26px;border-radius:50%;display:block}

/* footer */
.footer{left:0;top:4637px;width:1200px;height:478px;background:var(--navy-dark)}
.footer h4{font-weight:700;font-size:23px;color:var(--white)}
.flist{list-style:none;font-size:16px;color:var(--white);line-height:28px}
.flist li::before{content:"»";margin-right:12px}
.contact-row{display:flex;gap:24px;color:var(--white);font-size:16px;line-height:28px}
.contact-row i{flex:0 0 34px;height:34px;border-radius:50%;background:var(--sage-light);display:flex;align-items:center;justify-content:center}
</style>
</head>
<body>

<!-- HERO -->
<section class="abs hero" role="img" aria-label="Photo of a modern waterfront home with a pool and black powder coated pool fencing beside a garden path"></section>
<div class="abs logo"><i></i>Brightline Coatings Co</div>
<nav class="abs nav">
  <a class="active">Home</a><a>About</a><a>Products</a><a>Projects</a><a>Service Areas</a><a>Contact</a>
</nav>
<div class="abs hero-card">
  <h1>Design.<br><span>Fabrication.</span><br>Installation.</h1>
  <p>High-quality powder coated aluminium, stainless steel and glass solutions across the Whitsundays.</p>
  <div class="hero-btns">
    <span class="btn btn-navy" style="width:184px">Get a Free Quote</span>
    <span class="btn btn-sage" style="width:184px">View Our Work</span>
  </div>
</div>
<div class="abs" style="left:152px;top:646px;display:flex;gap:12px">
  <span class="circle-btn"><svg width="18" height="18" viewBox="0 0 18 18"><path d="M15 9H3M8 4 3 9l5 5" fill="none" stroke="#1f2a36" stroke-width="2"/></svg></span>
  <span class="circle-btn"><svg width="18" height="18" viewBox="0 0 18 18"><path d="M3 9h12M10 4l5 5-5 5" fill="none" stroke="#1f2a36" stroke-width="2"/></svg></span>
</div>
<div class="abs features">
  <div class="feature"><span class="ico"><svg width="26" height="26" viewBox="0 0 26 26" fill="none" stroke="#4f6a5f" stroke-width="2"><circle cx="9" cy="8" r="3"/><circle cx="17" cy="8" r="3"/><path d="M3 21c0-4 3-7 6-7s6 3 6 7M11 21c0-4 3-7 6-7s6 3 6 7"/></svg></span><span>Family Owned &amp;<br>Operated</span></div>
  <span class="fdiv"></span>
  <div class="feature"><span class="ico"><svg width="26" height="26" viewBox="0 0 26 26" fill="none" stroke="#4f6a5f" stroke-width="2"><path d="M8 22V12l5-7 1 7h6l-2 10z"/></svg></span><span>Quality<br>Craftsmanship</span></div>
  <span class="fdiv"></span>
  <div class="feature"><span class="ico"><svg width="26" height="26" viewBox="0 0 26 26" fill="none" stroke="#4f6a5f" stroke-width="2"><path d="M13 3l8 3v7c0 5-4 8-8 10-4-2-8-5-8-10V6z"/><path d="M9 13l3 3 5-6"/></svg></span><span>Durable &amp;<br>Reliable</span></div>
  <span class="fdiv"></span>
  <div class="feature"><span class="ico"><svg width="26" height="26" viewBox="0 0 26 26" fill="none" stroke="#4f6a5f" stroke-width="2"><circle cx="13" cy="11" r="7"/><path d="M9 17l-2 7 6-3 6 3-2-7"/></svg></span><span>Local Whitsundays<br>Experts</span></div>
</div>

<!-- ABOUT -->
<div class="abs" style="left:138px;top:1002px;width:440px;height:440px;border-radius:50%;border:8px solid var(--navy);padding:12px">
  <div role="img" aria-label="Photo of a timber deck with glass balustrade and outdoor lounge overlooking a beach" style="width:100%;height:100%;border-radius:50%;background:linear-gradient(180deg,#6e9fd0 0%,#a7c6df 40%,#8b6a4f 75%,#5a4332 100%)"></div>
</div>
<h2 class="abs sec-title" style="left:616px;top:1010px">ABOUT US</h2>
<div class="abs underline" style="left:618px;top:1070px;width:170px"></div>
<div class="abs subtitle" style="left:617px;top:1088px">A Family Business You Can Trust</div>
<p class="abs body" style="left:617px;top:1128px;width:440px;text-align:justify">BRIGHTLINE COATINGS CO operates as a reliable fence contractor located in Cannonvale, Queensland. This local business specializes in providing high-quality fencing solutions tailored to meet the needs of residential and commercial clients. With a focus on durability and aesthetics, BRIGHTLINE COATINGS CO offers a range of fencing options, including colorbond, timber, and pool fencing. The team prides itself on delivering exceptional craftsmanship and customer service, ensuring that each project is completed to the highest standards.</p>
<span class="abs btn btn-sage" style="left:617px;top:1378px;width:160px;height:44px">Learn More <svg width="16" height="12" viewBox="0 0 16 12"><path d="M1 6h13M9 1l5 5-5 5" fill="none" stroke="#fff" stroke-width="1.8"/></svg></span>

<!-- SERVICES -->
<h2 class="abs sec-title" style="left:0;width:1200px;text-align:center;top:1546px">OUR SERVICES</h2>
<div class="abs underline" style="left:520px;top:1604px;width:160px"></div>
<div class="abs subtitle" style="left:0;width:1200px;text-align:center;top:1628px">Quality Products That Enhance Your Space</div>
<div class="abs body" style="left:0;width:1200px;text-align:center;top:1660px">We design, fabricate and install a wide range of custom solutions tailored to your property</div>
<div class="svc" role="img" aria-label="Photo of white powder coated handrail on a balcony by the sea" style="left:16px;background:linear-gradient(180deg,#1e4ea8 0%,#5d86c4 45%,#cfd4d6 70%,#e8e8e6 100%)"></div>
<div class="svc" role="img" aria-label="Photo of white privacy slat screen and gate" style="left:415px;background:linear-gradient(180deg,#1d3f9a 0%,#6d8fc2 40%,#c9cccd 65%,#9a9c97 100%)"></div>
<div class="svc" role="img" aria-label="Photo of timber-look electric sliding gate" style="left:815px;background:linear-gradient(180deg,#e6e6e4 0%,#8a5a42 25%,#7a4d38 65%,#e9e9e8 100%)"></div>
<div class="svc-label" style="left:48px">Handrails</div>
<div class="svc-label" style="left:446px">Privacy Slat Screens</div>
<div class="svc-label" style="left:846px">Electric Gates</div>
<div class="abs" style="left:552px;top:2142px;display:flex;gap:12px">
  <span class="small-arrow"><svg width="16" height="16" viewBox="0 0 18 18"><path d="M15 9H3M8 4 3 9l5 5" fill="none" stroke="#1f2a36" stroke-width="2"/></svg></span>
  <span class="small-arrow"><svg width="16" height="16" viewBox="0 0 18 18"><path d="M3 9h12M10 4l5 5-5 5" fill="none" stroke="#1f2a36" stroke-width="2"/></svg></span>
</div>

<!-- EXPERTISE -->
<h2 class="abs sec-title" style="left:143px;top:2344px">OUR EXPERTISE</h2>
<div class="abs subtitle" style="left:144px;top:2424px">A Family Business You Can Trust</div>
<p class="abs body" style="left:144px;top:2464px;width:440px;text-align:justify">Beyond installation, we provide expert consultation to help you choose the right materials and designs to suit your space.</p>
<p class="abs body" style="left:144px;top:2536px;width:440px;text-align:justify">Our team works closely with you to ensure every project meets your expectations — combining functionality, aesthetics and long-term performance.</p>
<span class="abs btn btn-sage" style="left:144px;top:2624px;width:160px;height:44px">Learn More <svg width="16" height="12" viewBox="0 0 16 12"><path d="M1 6h13M9 1l5 5-5 5" fill="none" stroke="#fff" stroke-width="1.8"/></svg></span>
<div class="abs" style="left:630px;top:2366px;width:484px;height:5px;background:var(--sage)"></div>
<div class="photo" role="img" aria-label="Photo of a two-storey house with white balustrades" style="left:676px;top:2296px;width:178px;height:210px;background:linear-gradient(180deg,#2f63b4 0%,#9ab7d6 40%,#e9ecee 65%,#6a7a5a 100%)"></div>
<div class="photo" role="img" aria-label="Photo of white balcony balustrade under a ceiling fan" style="left:876px;top:2400px;width:178px;height:210px;background:linear-gradient(180deg,#c6c8c8 0%,#8f9496 50%,#dfe2e2 100%)"></div>
<div class="photo" role="img" aria-label="Photo of a rainforest creek with rocks" style="left:628px;top:2530px;width:226px;height:210px;background:linear-gradient(180deg,#2f5e30 0%,#4b8a6e 45%,#7a7566 100%)"></div>

<!-- SERVICE AREA -->
<section class="abs area"></section>
<h2 class="abs sec-title" style="left:0;width:1200px;text-align:center;top:2968px">SERVICE AREA</h2>
<div class="abs underline" style="left:520px;top:3026px;width:160px"></div>
<div class="abs subtitle" style="left:0;width:1200px;text-align:center;top:3048px">Servicing the Whitsundays &amp; North Queensland</div>
<div class="abs area-map" role="img" aria-label="Dotted map of Australia with location pins marking the service area"></div>
<div class="abs area-card">
  <ul>
    <li><i style="background:var(--navy)"></i>Whitsundays</li>
    <li><i style="background:var(--sage)"></i>Airlie Beach</li>
    <li><i style="background:var(--navy)"></i>Bowen</li>
    <li><i style="background:var(--sage)"></i>Mackay</li>
    <li><i style="background:var(--navy)"></i>Ayr</li>
    <li><i style="background:var(--sage)"></i>Townsville</li>
  </ul>
</div>

<!-- GALLERY -->
<h2 class="abs sec-title" style="left:0;width:1200px;text-align:center;top:3770px">OUR GALLERY</h2>
<div class="abs underline" style="left:520px;top:3828px;width:160px"></div>
<div class="photo" role="img" aria-label="Photo of black slat fencing in front of a house" style="left:143px;top:3865px;width:286px;height:282px;background:linear-gradient(180deg,#4a7cc4 0%,#e0e4e6 40%,#2a2c2e 75%,#7a8a5a 100%)"></div>
<div class="photo" role="img" aria-label="Photo of black pool fencing at a sports field" style="left:457px;top:3865px;width:286px;height:282px;background:linear-gradient(180deg,#2c64b5 0%,#8fb0d4 45%,#3f4a3a 75%,#6b8a4a 100%)"></div>
<div class="abs" style="left:578px;top:3984px;width:44px;height:44px;border-radius:50%;background:#fff;display:flex;align-items:center;justify-content:center"><svg width="16" height="16"><path d="M8 2v12M2 8h12" stroke="#1f2a36" stroke-width="2"/></svg></div>
<div class="photo" role="img" aria-label="Photo of pool with timber deck and fencing" style="left:771px;top:3865px;width:286px;height:282px;background:linear-gradient(180deg,#6a4a38 0%,#1f5a9a 40%,#2e78b8 60%,#7a5440 100%)"></div>
<div class="photo" role="img" aria-label="Photo of frameless glass pool fence under palm trees" style="left:143px;top:4171px;width:286px;height:282px;background:linear-gradient(180deg,#6d98c8 0%,#3f6a48 45%,#8ab0a8 70%,#b9b4a0 100%)"></div>
<div class="photo" role="img" aria-label="Photo of an outdoor dining table set on a deck" style="left:457px;top:4171px;width:286px;height:282px;background:linear-gradient(180deg,#1f2a20 0%,#3a2a20 40%,#6a3c2a 70%,#2c2420 100%)"></div>
<div class="photo" role="img" aria-label="Photo of a curved staircase with black handrail" style="left:771px;top:4171px;width:286px;height:282px;background:linear-gradient(180deg,#3f6fb8 0%,#c9bfa8 45%,#5a3e2a 100%)"></div>
<span class="abs btn btn-sage" style="left:496px;top:4472px;width:208px;height:44px">View More Photos <svg width="16" height="12" viewBox="0 0 16 12"><path d="M1 6h13M9 1l5 5-5 5" fill="none" stroke="#fff" stroke-width="1.8"/></svg></span>

<!-- FOOTER -->
<footer class="abs footer">
  <h4 class="abs" style="left:133px;top:96px">Quick Links</h4>
  <ul class="abs flist" style="left:133px;top:142px"><li>Home</li><li>About</li><li>Services</li><li>Gallery</li><li>FAQ</li><li>Contact</li></ul>
  <ul class="abs flist" style="left:300px;top:142px"><li>Privacy policy</li><li>Support</li><li>Terms &amp; Condition</li><li>FAQs</li><li>Blog</li></ul>
  <h4 class="abs" style="left:538px;top:96px">Services</h4>
  <ul class="abs flist" style="left:538px;top:142px"><li>Pool Fencing</li><li>Privacy Screens</li><li>Balustrades</li><li>Handrails</li><li>Electric Gates</li><li>Aluminium Fabrication</li><li>Powder Coating</li></ul>
  <h4 class="abs" style="left:792px;top:96px">Contact</h4>
  <div class="abs" style="left:792px;top:142px;width:300px">
    <div class="contact-row"><i><svg width="14" height="16" viewBox="0 0 14 18"><path d="M7 1a6 6 0 0 0-6 6c0 5 6 10 6 10s6-5 6-10a6 6 0 0 0-6-6z" fill="#fff"/><circle cx="7" cy="7" r="2" fill="#6f8a7f"/></svg></i><span>14 Harbourview Rd, Cannonvale, QLD, Australia, Queensland</span></div>
    <div class="contact-row" style="margin-top:18px"><i><svg width="14" height="14" viewBox="0 0 16 16"><path d="M3 1l3 3-2 2c1 2 3 4 5 5l2-2 3 3-2 3C7 14 2 9 1 3z" fill="#fff"/></svg></i><span style="line-height:34px">+61 400 555 182</span></div>
    <div class="contact-row" style="margin-top:22px"><i><svg width="14" height="12" viewBox="0 0 16 12"><rect x="1" y="1" width="14" height="10" fill="#fff"/><path d="M1 1l7 6 7-6" fill="none" stroke="#6f8a7f" stroke-width="1.5"/></svg></i><span style="line-height:34px">hello@brightlinecoatings.example</span></div>
  </div>
  <div class="abs" style="left:0;width:1200px;text-align:center;top:408px;color:#fff;font-size:16px">© Copyrights 2026 | All Rights Reserved</div>
</footer>

</body>
</html>
```